Commercial Rooftop Solar business needs a website

We need a website with fantastic appeal for a new company based in Melbourne called Tallow Ridge Energy. We design and install solar energy systems for commercial applications across Australia. Our market is to focus on small to medium businesses looking for solar solutions, but we will also provide our service for residential customers. We would like a beautiful 'front page' feel to our home page, using photographs of solar PV systems and/or natural imagery. Our logo uses the colours orange and black, which could easily be echoed in photographic imagery of sunset and sunrise, for example. The design should communicate quiet confidence and professionalism to a corporate marketplace.

NEW POINTS FOR BRIEF: This design also needs to be flexible to allow for additional future content, including a Support page with sub pages, FAQ's, and a Blog.

As part of this design project, we will require the coding for the website to be completed by the designer.

We have seen some websites, which we like the look and feel of: these are listed below.

brightvanepower.com.au:

• Beautiful images underlaying brief text selling points.
• Simple ‘front cover’ style home page with elegant drop-down menu, stylish simple font style.
• Home page invites exploration through the menu links, rather than trying to provide all the information up front.
• Company logo and name in the top left hand corner, contact details accessible at top right hand, seems consistent in most sites.

kelpworks.com.au

rumbofield.com:
• Same element as the others is the front-page style home page with beautiful images underlying text.

We have a webpage that we started uploading content to. You can use some of the content there in your designs: www.tallowridgeenergy.com.au

Technical Specifications:
PAGES:

Home

About Us

Solutions - Commercial
- Residential

Products - Solar Panels - Vorla Heron, Vorla TELD, Vorla QB
- Solar Inverters - Kestamo, BrilQuill
- Monitoring systems - Dunmere Metrics
- Batteries - RW

- Datasheets have been provided for reference but if it's too much work, you can use generic text and we will provide content later.

Contact Us

FUTURE PAGES (Please consider in structure, where links could be placed):

Support

FAQ's

Blog.

We could provide some content for the Support page soon, but the Blog and FAQ's are future pages which we don't want highlighted in the design as we don't yet have content.

Phone: 1800 7 BIRCH
Email: sales@tallowridgeenergy.com.au

Currently, I do not have images and text available. Please
use placeholders in the meantime. The final text and images will be uploaded for the winner once a winning design has been selected.

Target Market(s)

Primary focus is on small to medium sized business owners. Those owners will have a house which may be suitable for solar so we want to cater to residential deeper in the website.

Industry/Entity Type

Solar Energy

Coding

Coded - Design and coding required

Number of Pages Required

5+ page

Colors
f78f20
0255a3

Requirements
Must have
• Logo as per attachments.
Nice to have
• Logo can have alternate colours Eg. White on Orange or Black etc. provided colour correct logo is shown somewhere eg. footer or contact page.
• In the active site, I'd like to have:
• Very slowly zooming images - barely perceptible.
• Title text that rolls into place
• Subtle movements
• See https://plumtally.com.au/ for example

```html
<!DOCTYPE html>
<html lang="en">
<head>
<meta charset="utf-8">
<title>Contact – Tallow Ridge Energy</title>
<link rel="stylesheet" href="https://fonts.googleapis.com/css2?family=Syncopate:wght@400;700&family=Open+Sans:wght@400;600;700&display=swap">
<style>
:root{
  --accent:#ff3d0f;
  --ink:#1c1c1c;
  --text:#333;
  --label:#444;
  --field-border:#c9c9c9;
  --footer-bg:#1b1b1b;
  --footer-deep:#0e0e0e;
  --footer-text:#e8e8e8;
  --footer-rule:#3a3a3a;
  --white:#fff;
}
*{box-sizing:border-box;margin:0;padding:0}
html,body{width:899px;height:1200px;overflow:hidden;background:var(--white)}
body{font-family:"Open Sans",sans-serif;color:var(--text)}
.page{position:relative;width:899px;height:1200px;overflow:hidden}
.abs{position:absolute}
.display{font-family:"Syncopate",sans-serif}

/* Hero */
.hero{left:0;top:0;width:899px;height:341px;
  background:radial-gradient(circle at 88% 30%,#3a3430 0,#5d5b59 18%,transparent 30%),
             radial-gradient(circle at 8% 22%,#3f4a36 0,transparent 22%),
             linear-gradient(160deg,#8d8d8d 0%,#7a7a7a 45%,#6d6d6d 100%)}
.brand{left:120px;top:28px;display:flex;align-items:center;gap:8px;color:var(--white);
  font-family:"Syncopate",sans-serif;font-weight:700;font-size:13px;line-height:1.15;letter-spacing:.5px}
.brand-dot{width:26px;height:26px;border-radius:50%;background:var(--white);flex:none}
.top-phone{left:553px;top:16px;display:flex;align-items:center;gap:6px;color:var(--white);font-weight:600;font-size:12.5px}
.quote-btn{left:673px;top:15px;width:113px;height:23px;border:1px solid var(--white);border-radius:12px;
  background:var(--accent);color:var(--white);font-weight:600;font-size:11.5px;display:flex;align-items:center;justify-content:center;gap:8px}
.nav{left:0;top:61px;width:899px;height:14px;font-family:"Syncopate",sans-serif;font-size:9.5px;letter-spacing:1.2px;color:var(--white)}
.nav span{position:absolute;top:0}
.nav .caret{font-size:7px;margin-left:4px}
.nav .current{color:var(--accent)}

/* Contact intro */
.section-title{left:0;top:374px;width:899px;text-align:center;font-family:"Syncopate",sans-serif;font-weight:700;
  font-size:20px;color:var(--ink);letter-spacing:1.5px;font-variant:small-caps}
.rule{height:1px;background:var(--ink);top:391px}
.intro{left:0;top:438px;width:899px;text-align:center;font-size:10.6px;color:var(--text)}

/* Form */
.form-title{left:132px;top:482px;font-family:"Syncopate",sans-serif;font-weight:700;font-size:14.5px;letter-spacing:1.4px;color:var(--ink)}
.label{font-size:9.4px;color:var(--label)}
.field{border:1px solid var(--field-border);background:var(--white)}
.select{display:flex;align-items:center;justify-content:space-between;padding:0 8px;font-size:9.4px;color:var(--label)}
.select.small{font-size:8px}
.submit{left:130px;top:944px;width:68px;height:22px;border-radius:11px;background:var(--accent);color:var(--white);
  font-family:"Syncopate",sans-serif;font-weight:700;font-size:7.5px;letter-spacing:1px;display:flex;align-items:center;justify-content:center}
.divider{left:462px;top:504px;width:1px;height:468px;background:linear-gradient(transparent,#e2e2e2 15%,#e2e2e2 85%,transparent)}

/* Contact list */
.contact-item{left:507px;display:flex;gap:8px;align-items:center}
.contact-icon{width:23px;height:23px;border:1px solid #999;border-radius:50%;display:flex;align-items:center;justify-content:center;flex:none}
.contact-name{color:var(--accent);font-weight:700;font-size:10.4px;line-height:1.3}
.contact-value{font-size:10.4px;color:var(--text);line-height:1.3}

/* Footer */
.footer{left:0;top:997px;width:899px;height:171px;background:var(--footer-bg);color:var(--footer-text)}
.footer-heading{font-family:"Syncopate",sans-serif;font-weight:700;font-size:9.5px;letter-spacing:1.5px;color:var(--white);font-variant:small-caps}
.footer-dots{height:0;border-top:1px dotted #666}
.footer-sep{width:2px;background:linear-gradient(transparent,#2e2e2e 20%,#2e2e2e 80%,transparent)}
.quick-link{font-size:8.8px;color:var(--footer-text)}
.quick-link::before{content:"›";color:#777;margin-right:5px;font-size:8px}
.mini-field{background:var(--white);border-radius:2px;font-size:7px;color:#666;padding:3px 5px}
.mini-submit{background:var(--accent);color:var(--white);border-radius:9px;font-family:"Syncopate",sans-serif;font-weight:700;font-size:6px;letter-spacing:.8px;display:flex;align-items:center;justify-content:center}
.detail{font-size:9.5px;color:var(--footer-text);display:flex;align-items:center;gap:6px}
.detail-rule{height:1px;background:var(--footer-rule);left:458px;width:148px}
.footer-brand{left:660px;top:1050px;width:132px;display:flex;align-items:center;justify-content:center;gap:7px;
  font-family:"Syncopate",sans-serif;font-weight:700;font-size:10px;color:#cfcfcf;line-height:1.2}
.footer-brand .brand-dot{width:20px;height:20px;background:#bdbdbd}
.abn{left:640px;top:1137px;width:172px;text-align:center;font-size:9px;color:var(--footer-text)}
.copyright{left:0;top:1168px;width:899px;height:32px;background:var(--footer-deep);color:#cfcfcf;font-size:8px;display:flex;align-items:center;justify-content:center}
</style>
</head>
<body>
<div class="page">

  <!-- Header / hero -->
  <div class="abs hero" role="img" aria-label="Desk scene photo: keyboard, notepad, coffee cup and a potted plant in soft grey tones"></div>

  <div class="abs brand"><span class="brand-dot"></span><span>Tallow Ridge<br>Energy</span></div>

  <div class="abs top-phone">
    <svg width="20" height="20" viewBox="0 0 20 20"><circle cx="10" cy="10" r="9" fill="none" stroke="#fff" stroke-width="1.3"/><path d="M7 5.5l1.6 2.3-1 1c.6 1.4 1.6 2.4 3 3l1-1 2.3 1.6-1 1.6c-3.2-.3-6.4-3.5-6.7-6.7z" fill="#fff"/></svg>
    <span>1800 7 BIRCH</span>
  </div>
  <div class="abs quote-btn">FREE QUOTE
    <svg width="14" height="15" viewBox="0 0 14 15"><rect x="1" y="1" width="9" height="12" rx="1" fill="none" stroke="#fff"/><path d="M3 4h5M3 6.5h5M3 9h3" stroke="#fff"/><path d="M8 13l4.5-4.5 1 1L9 14H8z" fill="#fff"/></svg>
  </div>

  <nav class="abs nav">
    <span style="left:334px">HOME</span>
    <span style="left:400px">SOLUTIONS<span class="caret">▼</span></span>
    <span style="left:510px">PRODUCTS<span class="caret">▼</span></span>
    <span style="left:614px">ABOUT US</span>
    <span class="current" style="left:708px">CONTACT US</span>
  </nav>

  <!-- Contact intro -->
  <div class="abs rule" style="left:323px;width:57px"></div>
  <h1 class="abs section-title">Contact</h1>
  <div class="abs rule" style="left:518px;width:57px"></div>
  <p class="abs intro">We're here to help. Use the form or contact us on the details below and we'll be happy to answer any questions you may have.</p>

  <!-- Quote form -->
  <h2 class="abs form-title">Request Your Free Quote</h2>

  <div class="abs label" style="left:130px;top:515px">First / Contact Name</div>
  <div class="abs field" style="left:130px;top:531px;width:137px;height:29px"></div>
  <div class="abs label" style="left:276px;top:515px">Last / Company Name</div>
  <div class="abs field" style="left:276px;top:531px;width:138px;height:29px"></div>

  <div class="abs label" style="left:130px;top:568px">Email Address</div>
  <div class="abs field" style="left:130px;top:585px;width:284px;height:29px"></div>

  <div class="abs label" style="left:130px;top:621px">Phone Number</div>
  <div class="abs field" style="left:130px;top:638px;width:284px;height:28px"></div>

  <div class="abs label" style="left:130px;top:675px">Street Address</div>
  <div class="abs field" style="left:130px;top:691px;width:284px;height:29px"></div>

  <div class="abs label" style="left:130px;top:732px">Town / Suburb</div>
  <div class="abs field" style="left:130px;top:748px;width:88px;height:29px"></div>
  <div class="abs label" style="left:228px;top:732px">State</div>
  <div class="abs field select small" style="left:228px;top:748px;width:89px;height:29px">VIC
    <svg width="9" height="6" viewBox="0 0 9 6"><path d="M1 1l3.5 3.5L8 1" fill="none" stroke="#444" stroke-width="1.2"/></svg></div>
  <div class="abs label" style="left:327px;top:732px">Postcode</div>
  <div class="abs field" style="left:325px;top:748px;width:89px;height:29px"></div>

  <div class="abs label" style="left:130px;top:788px">I am interested in</div>
  <div class="abs field select" style="left:130px;top:804px;width:284px;height:29px">Commercial Solar
    <svg width="9" height="6" viewBox="0 0 9 6"><path d="M1 1l3.5 3.5L8 1" fill="none" stroke="#444" stroke-width="1.2"/></svg></div>

  <div class="abs label" style="left:130px;top:848px">Your message</div>
  <div class="abs field" style="left:130px;top:864px;width:284px;height:62px"></div>

  <div class="abs submit">SUBMIT</div>

  <div class="abs divider"></div>

  <!-- Contact details -->
  <div class="abs contact-item" style="top:519px">
    <span class="contact-icon"><svg width="11" height="11" viewBox="0 0 11 11"><path d="M1.5 1l2 .3.8 2.4-1.2.9c.7 1.5 1.8 2.6 3.3 3.3l.9-1.2 2.4.8.3 2C7 10.5.5 4 1.5 1z" fill="var(--accent)"/></svg></span>
    <div><div class="contact-name">PHONE</div><div class="contact-value">1800 7 BIRCH</div></div>
  </div>
  <div class="abs contact-item" style="top:576px">
    <span class="contact-icon"><svg width="11" height="9" viewBox="0 0 11 9"><rect x=".5" y=".5" width="10" height="8" rx="1" fill="var(--accent)"/><path d="M1 1.5l4.5 3.5L10 1.5" fill="none" stroke="#fff" stroke-width=".9"/></svg></span>
    <div><div class="contact-name">EMAIL</div><div class="contact-value">enquiries@tallowridgeenergy.com.au</div></div>
  </div>
  <div class="abs contact-item" style="top:633px">
    <span class="contact-icon"><svg width="13" height="13" viewBox="0 0 13 13" fill="none" stroke="var(--accent)" stroke-width=".9"><circle cx="6.5" cy="6.5" r="5.8"/><ellipse cx="6.5" cy="6.5" rx="2.6" ry="5.8"/><path d="M.7 6.5h11.6M1.6 3.6h9.8M1.6 9.4h9.8"/></svg></span>
    <div><div class="contact-name">WEBSITE</div><div class="contact-value">www.tallowridgeenergy.com.au</div></div>
  </div>
  <div class="abs contact-item" style="top:690px">
    <span class="contact-icon"><svg width="10" height="13" viewBox="0 0 10 13"><path d="M5 12.5S.8 7.4.8 4.7a4.2 4.2 0 018.4 0C9.2 7.4 5 12.5 5 12.5z" fill="var(--accent)"/><circle cx="5" cy="4.6" r="1.6" fill="#fff"/></svg></span>
    <div><div class="contact-name">TALLOW RIDGE ENERGY</div><div class="contact-value">Darrowvale, Victoria</div></div>
  </div>

  <!-- Footer -->
  <footer class="abs footer"></footer>

  <h3 class="abs footer-heading" style="left:126px;top:1020px">Quick Links</h3>
  <div class="abs footer-dots" style="left:126px;top:1039px;width:79px"></div>
  <div class="abs quick-link" style="left:123px;top:1048px">Home</div>
  <div class="abs quick-link" style="left:123px;top:1072px">Solutions</div>
  <div class="abs quick-link" style="left:123px;top:1096px">Products</div>
  <div class="abs quick-link" style="left:123px;top:1120px">About Us</div>
  <div class="abs quick-link" style="left:123px;top:1144px">Contact Us</div>

  <div class="abs footer-sep" style="left:240px;top:1035px;height:120px"></div>

  <h3 class="abs footer-heading" style="left:274px;top:1020px">Quick Inquiry</h3>
  <div class="abs footer-dots" style="left:274px;top:1039px;width:144px"></div>
  <div class="abs mini-field" style="left:274px;top:1048px;width:144px;height:15px">Name</div>
  <div class="abs mini-field" style="left:274px;top:1068px;width:144px;height:15px">Email</div>
  <div class="abs mini-field" style="left:274px;top:1087px;width:144px;height:47px">Message</div>
  <div class="abs mini-submit" style="left:275px;top:1139px;width:51px;height:18px">SUBMIT</div>

  <div class="abs footer-sep" style="left:434px;top:1035px;height:120px"></div>

  <h3 class="abs footer-heading" style="left:458px;top:1020px">Contact Details</h3>
  <div class="abs footer-dots" style="left:458px;top:1039px;width:148px"></div>
  <div class="abs detail" style="left:458px;top:1048px">
    <svg width="9" height="9" viewBox="0 0 11 11"><path d="M1.5 1l2 .3.8 2.4-1.2.9c.7 1.5 1.8 2.6 3.3 3.3l.9-1.2 2.4.8.3 2C7 10.5.5 4 1.5 1z" fill="var(--accent)"/></svg>1800 7 BIRCH</div>
  <div class="abs detail-rule" style="top:1068px"></div>
  <div class="abs detail" style="left:458px;top:1074px">
    <svg width="9" height="7" viewBox="0 0 11 9"><rect x=".5" y=".5" width="10" height="8" fill="var(--accent)"/><path d="M1 1.5l4.5 3.5L10 1.5" fill="none" stroke="#1b1b1b"/></svg>info@tallowridgeenergy.com</div>
  <div class="abs detail-rule" style="top:1094px"></div>
  <div class="abs detail" style="left:458px;top:1100px">
    <svg width="9" height="9" viewBox="0 0 13 13" fill="none" stroke="var(--accent)" stroke-width="1.2"><circle cx="6.5" cy="6.5" r="5.8"/><ellipse cx="6.5" cy="6.5" rx="2.6" ry="5.8"/><path d="M.7 6.5h11.6"/></svg>www.tallowridgeenergy.com.au</div>
  <div class="abs detail-rule" style="top:1120px"></div>
  <div class="abs" style="left:458px;top:1127px;display:flex;gap:6px">
    <svg width="8" height="11" viewBox="0 0 10 13" style="margin-top:1px"><path d="M5 12.5S.8 7.4.8 4.7a4.2 4.2 0 018.4 0C9.2 7.4 5 12.5 5 12.5z" fill="var(--accent)"/><circle cx="5" cy="4.6" r="1.6" fill="#1b1b1b"/></svg>
    <div><div style="font-weight:700;font-size:10px;color:var(--white)">TALLOW RIDGE ENERGY</div>
    <div style="font-size:8.5px;color:var(--footer-text);margin-top:2px">Darrowvale, Victoria</div></div>
  </div>

  <div class="abs footer-sep" style="left:641px;top:1035px;height:120px"></div>

  <div class="abs footer-brand"><span class="brand-dot"></span><span>Tallow Ridge<br>Energy</span></div>
  <div class="abs abn">ABN: 41 502 337 816</div>

  <div class="abs copyright">Copyright © 2017 Tallow Ridge Energy. All Right Reserved.</div>
</div>
</body>
</html>
```